Building company buisness cards

We are looking for a sharp modern new look for our business cards.
We are a New Zealand based company that specialises in house and land packages.
We have attached a photo of the current logo and would like to see if it can be improved somehow if needed.
We are open to any colours but we have chosen green at this stage.
Feel free to change the font and make the logo smarter looking.
Play with the colours and see what looks best.

We want a card that looks so good know one will want to throw it away!

Target Market(s)

Home buyers

Industry/Entity Type

Building

Contact Information for Business Card

Derek Tolvane
0217394062
dtolvane@quillmarkhomesteads.co.nz
quillmarkhomesteads.co.nz

Font styles to use
Serif
Sans Serif

Colors

Designer to choose colors to be used in the design.

Requirements
Must have
• Logo and company name on one side, details on the other side
Nice to have
• Color codes for the original green are HEX #4a8028, RGB(74,128,40), CMYK(42,0,69,50)
• Round corners, Raised and/or spot UV

```html
<!DOCTYPE html>
<html lang="en">
<head>
<meta charset="utf-8">
<title>Quillmark Homesteads – Business Card</title>
<link href="https://fonts.googleapis.com/css2?family=Montserrat:wght@400;700&display=swap" rel="stylesheet">
<style>
  :root {
    --brand-green: #4a8028;
    --paper: #ffffff;
    --ink: #2b2b2b;
    --stripe-grey: #b3b3b3;
    --backdrop: #e9eaea;
  }
  * { box-sizing: border-box; margin: 0; padding: 0; }
  html, body { width: 1200px; height: 900px; overflow: hidden; }
  body {
    background: var(--backdrop);
    font-family: "Montserrat", sans-serif;
    position: relative;
  }
  .card {
    position: absolute;
    left: 250px;
    width: 700px;
    height: 400px;
    border-radius: 26px;
    overflow: hidden;
    box-shadow: 0 6px 18px rgba(0,0,0,0.18);
  }
  .card--back { top: 35px; background: var(--brand-green); }
  .card--front { top: 465px; background: var(--paper); }

  .brand-square { position: absolute; width: 40px; height: 40px; }
  .card--back .brand-square { left: 330px; top: 92px; background: var(--paper); }
  .card--front .brand-square { right: 48px; top: 36px; background: var(--brand-green); }

  .company-name {
    position: absolute;
    font-family: "Montserrat", sans-serif;
    font-weight: 700;
    line-height: 1.1;
  }
  .card--back .company-name {
    left: 0; right: 0; top: 150px;
    text-align: center;
    color: var(--paper);
    font-size: 44px;
  }
  .card--back .website {
    position: absolute; left: 0; right: 0; top: 290px;
    text-align: center;
    color: var(--paper);
    font-size: 17px;
    letter-spacing: 0.3px;
  }

  .holder { position: absolute; left: 42px; top: 60px; }
  .holder__name { color: var(--brand-green); font-weight: 700; font-size: 22px; }
  .holder__role { color: var(--ink); font-size: 17px; margin-top: 2px; }
  .card--front .company-name {
    right: 48px; top: 86px;
    text-align: right;
    color: var(--brand-green);
    font-size: 30px;
  }
  .divider {
    position: absolute; left: 42px; right: 40px; top: 168px;
    height: 2px; background: var(--brand-green);
  }
  .contacts {
    position: absolute; left: 42px; top: 184px;
    list-style: none; color: var(--ink); font-size: 16px;
  }
  .contacts li { display: flex; align-items: center; gap: 8px; height: 24px; }
  .contacts svg { width: 13px; height: 13px; flex: none; }
  .swoosh { position: absolute; left: 0; bottom: 0; width: 700px; height: 400px; }
</style>
</head>
<body>

  <section class="card card--back" aria-label="Card back">
    <div class="brand-square" aria-hidden="true"></div>
    <p class="company-name">Quillmark<br>Homesteads</p>
    <p class="website">quillmarkhomesteads.co.nz</p>
  </section>

  <section class="card card--front" aria-label="Card front">
    <svg class="swoosh" viewBox="0 0 700 400" aria-hidden="true">
      <path d="M0 272 C120 262 200 300 290 345 C380 392 520 392 700 388 L700 400 L0 400 Z" fill="var(--stripe-grey)"/>
      <path d="M0 282 C120 275 200 312 290 355 C380 398 520 398 700 398 L700 400 L0 400 Z" fill="var(--brand-green)"/>
    </svg>

    <div class="holder">
      <p class="holder__name">Derek Tolvane</p>
      <p class="holder__role">Founder</p>
    </div>

    <div class="brand-square" aria-hidden="true"></div>
    <p class="company-name">Quillmark<br>Homesteads</p>

    <div class="divider"></div>

    <ul class="contacts">
      <li>
        <svg viewBox="0 0 24 24" aria-hidden="true"><path d="M6.6 10.8a15 15 0 0 0 6.6 6.6l2.2-2.2a1 1 0 0 1 1-.25 11.4 11.4 0 0 0 3.6.6 1 1 0 0 1 1 1V20a1 1 0 0 1-1 1A17 17 0 0 1 3 4a1 1 0 0 1 1-1h3.5a1 1 0 0 1 1 1c0 1.25.2 2.45.6 3.6a1 1 0 0 1-.25 1z" fill="var(--brand-green)"/></svg>
        0217394062
      </li>
      <li>
        <svg viewBox="0 0 24 24" aria-hidden="true"><rect x="2" y="5" width="20" height="14" rx="1.5" fill="none" stroke="var(--brand-green)" stroke-width="2"/><path d="M2.5 6l9.5 7 9.5-7" fill="none" stroke="var(--brand-green)" stroke-width="2"/></svg>
        dtolvane@quillmarkhomesteads.co.nz
      </li>
      <li>
        <svg viewBox="0 0 24 24" aria-hidden="true"><circle cx="12" cy="12" r="10" fill="none" stroke="var(--brand-green)" stroke-width="2"/><path d="M2 12h20M12 2c3 3 3 17 0 20M12 2c-3 3-3 17 0 20" fill="none" stroke="var(--brand-green)" stroke-width="1.6"/></svg>
        quillmarkhomesteads.co.nz
      </li>
    </ul>
  </section>

</body>
</html>
```